Colin Vardek Business card

Hey there, I’m hoping to have a business card designed. I’m in Real estate and just switched to a new Brokerage called: The Harbourline Property Group

The back could just be the company name maybe or whatever looks good!

I’ve attached some logos of our company and some cards my buddy had done up.

On the card:
Colin Vardek
colinvardek@mailora.com
587-412-9065
colinvardek.ca

Target Market(s)

Home buyers and sellers

Industry/Entity Type

Real Estate

Contact Information for Business Card

just looking for a cool and modern design with my picture on it. I like the idea of Black and red being used.

Requirements
Must have
• all the details provided. I'm open to anything. Just want a professional looking card.

```html
<!DOCTYPE html>
<html lang="en">
<head>
<meta charset="UTF-8">
<title>Colin Vardek – Business Card</title>
<link href="https://fonts.googleapis.com/css2?family=Poppins:wght@300;400;600;700&display=swap" rel="stylesheet">
<style>
  :root {
    --stage: #222224;
    --card: #232326;
    --card-edge: #d3192b;
    --red: #d62238;
    --white: #ffffff;
    --muted: #e6e6e6;
    --photo-dark: #1b1c20;
    --photo-mid: #3a3436;
    --photo-skin: #8a6a5c;
  }
  * { margin: 0; padding: 0; box-sizing: border-box; }
  html, body {
    width: 1200px; height: 711px; overflow: hidden;
    background: var(--stage);
    font-family: "Poppins", sans-serif;
  }
  .stage {
    position: relative; width: 1200px; height: 711px;
    display: flex; align-items: center; justify-content: center; gap: 40px;
  }
  .card {
    position: relative; width: 520px; height: 297px;
    background: var(--card);
    border-radius: 18px;
    border-bottom: 3px solid var(--card-edge);
    border-left: 2px solid var(--card-edge);
    box-shadow: 0 14px 30px rgba(0,0,0,0.55);
    overflow: hidden;
  }
  /* Front */
  .card--front { display: flex; align-items: center; justify-content: center; }
  .brand-mark {
    display: flex; align-items: center; gap: 14px;
  }
  .brand-mark__square { width: 22px; height: 22px; background: var(--red); }
  .brand-mark__name {
    color: var(--red); font-weight: 600; font-size: 25px; line-height: 1.15;
    max-width: 330px;
  }
  /* Back */
  .card__brand {
    position: absolute; left: 28px; top: 36px;
    display: flex; align-items: center; gap: 10px;
  }
  .card__brand-square { width: 14px; height: 14px; background: var(--red); }
  .card__brand-name {
    color: var(--white); font-weight: 600; font-size: 17px; line-height: 1.15; max-width: 220px;
  }
  .portrait {
    position: absolute; right: 0; top: 40px; width: 200px; height: 257px;
    background:
      radial-gradient(ellipse 60px 75px at 50% 30%, var(--photo-skin), transparent 70%),
      linear-gradient(180deg, var(--photo-mid) 0%, var(--photo-dark) 100%);
    border-radius: 90px 90px 0 0;
  }
  .identity {
    position: absolute; left: 0; top: 168px;
    display: flex; align-items: center; gap: 12px;
  }
  .identity__bar { width: 14px; height: 34px; background: var(--red); }
  .identity__name { font-size: 27px; line-height: 1; }
  .identity__first { color: var(--red); font-weight: 700; }
  .identity__last { color: var(--white); font-weight: 300; }
  .contacts {
    position: absolute; left: 40px; top: 218px; list-style: none;
  }
  .contacts__item {
    display: flex; align-items: center; gap: 9px;
    color: var(--muted); font-size: 12.5px; font-weight: 400; line-height: 22px;
  }
  .contacts__icon { width: 13px; height: 13px; flex: none; }
</style>
</head>
<body>
<main class="stage">
  <section class="card card--front" aria-label="Card front">
    <div class="brand-mark">
      <span class="brand-mark__square"></span>
      <span class="brand-mark__name">The Harbourline Property Group</span>
    </div>
  </section>

  <section class="card card--back" aria-label="Card back">
    <div class="card__brand">
      <span class="card__brand-square"></span>
      <span class="card__brand-name">The Harbourline Property Group</span>
    </div>

    <div class="portrait" role="img" aria-label="Portrait photo of Colin Vardek in a dark blazer and white shirt"></div>

    <div class="identity">
      <span class="identity__bar"></span>
      <h1 class="identity__name"><span class="identity__first">Colin</span> <span class="identity__last">Vardek</span></h1>
    </div>

    <ul class="contacts">
      <li class="contacts__item">
        <svg class="contacts__icon" viewBox="0 0 16 16" aria-hidden="true"><path fill="var(--red)" d="M3.5 1.5l2.5 0 1 3.5-1.8 1.2a9 9 0 0 0 4.6 4.6L11 9l3.5 1v2.5c0 1-1 2-2 2A11 11 0 0 1 1.5 3.5c0-1 1-2 2-2z"/></svg>
        587-412-9065
      </li>
      <li class="contacts__item">
        <svg class="contacts__icon" viewBox="0 0 16 16" aria-hidden="true"><g fill="none" stroke="var(--red)" stroke-width="1.6"><circle cx="8" cy="8" r="6.5"/><ellipse cx="8" cy="8" rx="3" ry="6.5"/><path d="M1.5 8h13"/></g></svg>
        www.colinvardek.ca
      </li>
      <li class="contacts__item">
        <svg class="contacts__icon" viewBox="0 0 16 16" aria-hidden="true"><rect x="1.5" y="3.5" width="13" height="9" rx="1" fill="var(--red)"/><path d="M2 4.5l6 4.5 6-4.5" fill="none" stroke="var(--card)" stroke-width="1.3"/></svg>
        colinvardek@mailora.com
      </li>
    </ul>
  </section>
</main>
</body>
</html>
```